bamboo kettle vietnamese restaurant in need of a new menu

a family owned vietnamese restaurant in need of a new menu design that is fun, classy, and yet simple. menu that will catch the customers eyes. easy to read yet flows nicely. like to use the color green (basil green color) creme yellow and maroon. open to other colors as long as it looks nice together. our restaurant is family oriented, casual yet has a nice ambiance atmosphere.
prefer 11x17 portrait double sided. attached is our menu with the current price updated so use the info on this to start creating! looking for something unique, professional and one of a kind menu!
Updates
please use your own creative layout and design. we are open to ideas. the files uploaded are the updated prices and the logo is to use whichever one you feel goes with the menu.
Reason: don't see anything we like so far...please be creative!
Target Market(s)
restaurant consumers
Industry/Entity Type
Restaurant
Look and feel

```html
<!DOCTYPE html>
<html lang="en">
<head>
<meta charset="utf-8">
<title>Bamboo Kettle Menu</title>
<link href="https://fonts.googleapis.com/css2?family=League+Gothic&family=Oswald:wght@300;400&display=swap" rel="stylesheet">
<style>
:root{
  --basil:#72b53c;
  --basil-light:#8cc63f;
  --leaf-wash:#e6f1dc;
  --ink:#222;
  --muted:#555;
  --paper:#fff;
  --chili:#f07a1a;
}
*{box-sizing:border-box;margin:0;padding:0}
html,body{width:1200px;height:777px;overflow:hidden;background:var(--paper)}
.menu{position:relative;width:1200px;height:777px;overflow:hidden;font-family:"Oswald",sans-serif;color:var(--ink);text-transform:uppercase}
.leaf-wash{position:absolute;border-radius:50%;background:radial-gradient(closest-side,var(--leaf-wash),rgba(230,241,220,0))}
.heading{font-family:"League Gothic",sans-serif;font-weight:400;color:var(--basil);line-height:.85;letter-spacing:1px}
.heading.big{font-size:58px}
.heading.mid{font-size:50px}
.section-head{position:absolute}
.section-head.centered{text-align:center}
.section-head.inline{display:flex;align-items:flex-start;gap:6px}
.section-head .tagline{display:flex;flex-direction:column;padding-top:3px}
.subhead{font-family:"Oswald",sans-serif;font-weight:300;font-size:13px;line-height:1.05;color:var(--ink)}
.note{font-weight:300;font-size:8px;line-height:1.3;color:var(--ink)}
.note.soft{color:var(--muted);font-size:8.4px;line-height:1.2}
.free-note{position:absolute}
.col{position:absolute}
.item{display:flex;margin-bottom:5px}
.item .no{width:16px;flex:none;font-weight:400;font-size:10px;line-height:1.15}
.item .name{font-weight:400;font-size:10px;line-height:1.15}
.item .name.lg{font-size:11.5px}
.item .price{font-weight:300;color:var(--basil-light);margin-left:3px}
.item .desc{font-weight:300;font-size:8px;line-height:1.25;color:var(--muted);display:block}
.hot{display:inline-block;width:7px;height:9px;vertical-align:-1px;margin-left:1px}
.photo{position:absolute;border-radius:50%;border:4px solid #fff}
.extras{position:absolute;left:422px;top:370px;color:#fff;font-weight:300;font-size:6.2px;line-height:1.32}
</style>
</head>
<body>
<main class="menu">
  <div class="leaf-wash" role="img" aria-label="Watercolour basil leaves" style="left:-60px;top:-60px;width:260px;height:240px"></div>
  <div class="leaf-wash" role="img" aria-label="Watercolour basil leaves" style="left:-80px;top:560px;width:340px;height:260px"></div>
  <div class="leaf-wash" role="img" aria-label="Watercolour basil leaves" style="left:300px;top:-50px;width:260px;height:200px"></div>
  <div class="leaf-wash" role="img" aria-label="Watercolour basil leaves" style="left:480px;top:140px;width:200px;height:260px"></div>
  <div class="leaf-wash" role="img" aria-label="Watercolour basil leaves" style="left:880px;top:240px;width:260px;height:220px"></div>
  <div class="leaf-wash" role="img" aria-label="Watercolour basil leaves" style="left:980px;top:560px;width:300px;height:260px"></div>

  <!-- Appetizers -->
  <div class="section-head centered" style="left:29px;top:22px;width:350px"><h2 class="heading big">Appetizers</h2></div>
  <p class="note free-note" style="left:29px;top:74px;width:350px">Spring rolls (2) comes with lettuce, vermicelli noodles rolled in rice paper served with peanut sauce with choice of: (cannot be mixed):</p>
  <div class="col" style="left:40px;top:106px;width:160px">
    <div class="item"><span class="no">1.</span><span class="name">Goi Cuon Tom &amp; Thit Heo<span class="price">4.50</span><span class="desc">Shrimp &amp; pork spring rolls</span></span></div>
    <div class="item"><span class="no">2.</span><span class="name">Goi Cuon Thit Heo / Ga / or Bo Nuong<span class="price">5.50</span><span class="desc">Choice of: grilled pork / grilled chicken or grilled beef spring rolls</span></span></div>
    <div class="item"><span class="no">3.</span><span class="name">Bi Cuon<span class="price">4.50</span><span class="desc">Pork skin roasted with rice powder spring rolls</span></span></div>
    <div class="item"><span class="no">4.</span><span class="name">Cha Gio (2)<span class="price">4.50</span><span class="desc">Fried eggrolls with shrimp, pork &amp; vegetables rolled in egg wrap</span></span></div>
    <div class="item"><span class="no">5.</span><span class="name">Canh Ga Nuoc Mam (6)<span class="price">7.95</span><span class="desc">Fried chicken wings</span></span></div>
  </div>
  <div class="col" style="left:210px;top:106px;width:160px">
    <div class="item"><span class="no">6.</span><span class="name">Gio Tom (4)<span class="price">5.95</span><span class="desc">Fried shrimp rolls</span></span></div>
    <div class="item"><span class="no">7.</span><span class="name">Ca Vien Chien (8)<span class="price">4.95</span><span class="desc">Fried fish balls</span></span></div>
    <div class="item"><span class="no">8.</span><span class="name">Chao Tom (2)<span class="price">7.95</span><span class="desc">Grilled shrimp paste wrapped around sugar cane stick</span></span></div>
    <div class="item"><span class="no">9.</span><span class="name">Wonton Soup<span class="price">(S) 4.95 (L) 7.50</span><span class="desc">Wonton shrimp &amp; pork soup</span></span></div>
    <div class="item"><span class="no">10.</span><span class="name">Tom Cua Soup<span class="price">(S) 4.95 (L) 7.50</span><span class="desc">Crab meat, shrimp &amp; egg soup</span></span></div>
  </div>
  <p class="note free-note" style="left:29px;top:309px;width:350px">Vietnamese salad comes with thin cabbage, carrots, onions, mints, crushed peanuts tossed in lime juice &amp; vinegar with the following choices of:</p>
  <div class="col" style="left:40px;top:336px;width:160px">
    <div class="item"><span class="no">11.</span><span class="name lg">Goi Ga<span class="price">8.95</span><span class="desc">Chicken salad</span></span></div>
    <div class="item"><span class="no">12.</span><span class="name lg">Goi Tom<span class="price">9.95</span><span class="desc">Shrimp salad</span></span></div>
  </div>
  <div class="col" style="left:210px;top:338px;width:155px">
    <div class="item"><span class="no">13.</span><span class="name lg">Bo Tai Chanh<span class="price">11.95</span><span class="desc">Rare thin sliced beef with onions, mints, basils, crushed peanuts in lime juice &amp; vinegar</span></span></div>
    <div class="item"><span class="no">14.</span><span class="name lg">Chim Cut Roti<span class="price">11.95</span><span class="desc">Roasted quails served with salt &amp; pepper</span></span></div>
  </div>

  <!-- Hu Tieu -->
  <div class="section-head" style="left:29px;top:412px">
    <h2 class="heading big">Hu Tieu (Mi)</h2>
    <p class="subhead" style="margin-top:-2px">Noodle Soup</p>
    <p class="note">Pork broth with rice or egg noodle</p>
  </div>
  <div class="col" style="left:40px;top:486px;width:330px">
    <div class="item"><span class="no">15.</span><span class="name">Hu Tieu Mi Dac Biet<span class="price">10.50</span><span class="desc">Choice of: rice or egg noodle with shrimp, roast pork, chicken, imitation crab, quail eggs, ground pork &amp; fried shrimp cracker combination noodle soup</span></span></div>
    <div class="item"><span class="no">16.</span><span class="name">Hu Tieu Mi Hai San<span class="price">11.50</span><span class="desc">Choice of: rice or egg noodle with shrimp, scallop, squid, fish balls &amp; imitation crab noodle soup</span></span></div>
    <div class="item"><span class="no">17.</span><span class="name">Hu Tieu Mytho<span class="price">9.95</span><span class="desc">Shrimp, roast pork, chicken, fish ball, imitation crab &amp; ground pork with clear noodle soup</span></span></div>
    <div class="item"><span class="no">18.</span><span class="name">Hu Tieu Sate<span class="price">9.50</span><svg class="hot" viewBox="0 0 10 13"><path d="M5 0C6 4 10 5 9 9a4 4 0 0 1-8 0C1 6 3 5 3 3c1 1 2 2 2 3 1-2 0-4 0-6z" fill="var(--chili)"/></svg><span class="desc">Choice of: rice or egg noodle with shrimp, roast pork, chicken, imitation crab, ground pork and fried shrimp cracker with soup on the side</span></span></div>
  </div>
  <div class="col" style="left:40px;top:653px;width:165px">
    <div class="item"><span class="no">19.</span><span class="name">Hu Tieu Mi Kho Dac Biet<span class="price">10.95</span><span class="desc">Fried chicken wings</span></span></div>
    <div class="item" style="margin-bottom:1px"><span class="no">20.</span><span class="name">Mi Hoanh Thanh<span class="price">8.95</span><span class="desc">Wonton with egg noodle soup</span></span></div>
    <div class="item"><span class="no">21.</span><span class="name">+Xa Xiu (Roast Pork)<span class="price">10.95</span></span></div>
  </div>
  <div class="col" style="left:212px;top:651px;width:160px">
    <div class="item"><span class="no">22.</span><span class="name lg">Banh Canh Tom Thit Gio Heo<span class="price">9.50</span><span class="desc">Shrimp, pork knuckle &amp; Vietnamese big noodle soup</span></span></div>
    <div class="item"><span class="no">23.</span><span class="name lg">Banh Canh Ga<span class="price">8.95</span><span class="desc">Chicken with Vietnamese big noodle soup</span></span></div>
  </div>

  <!-- Pho -->
  <div class="section-head centered" style="left:500px;top:22px;width:200px">
    <h2 class="heading big">Pho</h2>
    <p class="subhead">Rice Noodles Soup</p>
  </div>
  <div class="col" style="left:438px;top:106px;width:165px">
    <div class="item"><span class="no">24.</span><span class="name">Pho Dac Biet<span class="price">9.50</span><span class="desc">Steak, brisket, flank, tendon, tripe &amp; meatballs combination noodle soup</span></span></div>
    <div class="item"><span class="no">25.</span><span class="name">Pho<span class="price">8.50</span><span class="desc">Noodle soup with choices up to 3 items: steak, brisket, flank, tendon, tripe, meatball or vegetables</span></span></div>
    <div class="item"><span class="no">26.</span><span class="name">Pho Ga Vietnam (Ga Di Bo)<span class="price">10.50</span><span class="desc">Free range chicken noodle soup</span></span></div>
    <div class="item"><span class="no">27.</span><span class="name">Pho Ga My<span class="price">9.50</span><span class="desc">White chicken &amp; mixed vegetables noodle soup</span></span></div>
    <div class="item"><span class="no">28.</span><span class="name">Pho Thit Heo / Bo / or Ga Nuong<span class="price">10.50</span><span class="desc">Choice of: grilled pork, grilled beef or grilled chicken with mixed vegetables noodle soup</span></span></div>
  </div>
  <div class="col" style="left:610px;top:106px;width:170px">
    <div class="item"><span class="no">29.</span><span class="name">Pho Do Bien<span class="price">11.50</span><span class="desc">Shrimp, scallop, squid, fish balls, imitation crab &amp; vegetables seafood noodle soup</span></span></div>
    <div class="item"><span class="no">30.</span><span class="name">Pho Tom<span class="price">9.75</span><span class="desc">Shrimp with mixed vegetables noodle soup</span></span></div>
    <div class="item"><span class="no">31.</span><span class="name">Pho Do Bien Chua Cay<span class="price">11.50</span><svg class="hot" viewBox="0 0 10 13"><path d="M5 0C6 4 10 5 9 9a4 4 0 0 1-8 0C1 6 3 5 3 3c1 1 2 2 2 3 1-2 0-4 0-6z" fill="var(--chili)"/></svg><span class="desc">Shrimp, scallop, squid, fish balls &amp; imitation crab in hot &amp; sour noodle soup</span></span></div>
    <div class="item"><span class="no">32.</span><span class="name">Pho Tre Em<span class="price">7.25</span><span class="desc">Kid's steak &amp; meatball noodle soup</span></span></div>
  </div>

  <svg style="position:absolute;left:400px;top:364px" width="400" height="92" aria-hidden="true">
    <rect x="0" y="0" width="230" height="90" fill="var(--basil)" opacity=".85"/>
    <rect x="230" y="0" width="170" height="18" fill="var(--basil)" opacity=".85"/>
    <rect x="230" y="25" width="150" height="16" fill="var(--basil)" opacity=".85"/>
    <rect x="230" y="48" width="130" height="16" fill="var(--basil)" opacity=".85"/>
    <rect x="230" y="71" width="110" height="14" fill="var(--basil)" opacity=".85"/>
  </svg>
  <div class="extras">
    • X-Large 2.00 more<br>• Extra meat (steak, chicken, etc.) 3.50<br>• Extra shrimp 3.00<br>• Extra herbs or vegetables 1.50<br>&nbsp;&nbsp;(ex: onions, cilantros, basils, beansprouts, etc.)<br>• Extra rice, soup or noodles 1.50<br>• Change noodle or brown rice 2.00<br>• Add fried egg 1.50<br>• Add or change to fried rice 3.00<br>• Add eggroll 2.25
  </div>
  <div class="photo" role="img" aria-label="Bowl of pho with beef and noodles" style="left:602px;top:336px;width:124px;height:124px;background:radial-gradient(circle,#d9b37a 0%,#c7955a 45%,#f4efe6 62%,#e8e2d8 100%)"></div>

  <!-- Bun -->
  <div class="section-head inline" style="left:412px;top:474px">
    <h2 class="heading mid">Bun</h2>
    <div class="tagline">
      <p class="subhead">Vermicelli Noodle Bowl</p>
      <p class="note soft" style="width:330px;margin-top:2px">All vermicelli bowl comes with fresh lettuce, bean sprouts, sliced cucumbers, shredded carrots &amp; crushed peanuts</p>
    </div>
  </div>
  <div class="col" style="left:437px;top:534px;width:165px">
    <div class="item"><span class="no">33.</span><span class="name">Bun Dac Biet<span class="price">12.95</span><span class="desc">Choice of: grilled pork, grilled chicken or grilled beef with grilled shrimp &amp; fried eggroll special combination vermicelli bowl</span></span></div>
    <div class="item"><span class="no">34.</span><span class="name">Bun - Vermicelli Bowl<span class="price">9.50</span><span class="desc">Choice of: grilled pork, grilled chicken or grilled beef</span></span></div>
    <div class="item" style="margin-bottom:1px"><span class="no">35.</span><span class="name">+ Eggroll<span class="price">9.50</span></span></div>
    <div class="item"><span class="no">36.</span><span class="name">+ Shrimp<span class="price">10.50</span></span></div>
    <div class="item"><span class="no">37.</span><span class="name">Bun Tom Nuong (8)<span class="price">10.50</span><span class="desc">Grilled shrimp vermicelli bowl</span></span></div>
  </div>
  <div class="col" style="left:609px;top:534px;width:160px">
    <div class="item"><span class="no">38.</span><span class="name">Bun Cha Gio (3)<span class="price">9.50</span><span class="desc">Fried eggroll vermicelli bowl</span></span></div>
    <div class="item"><span class="no">39.</span><span class="name">Bun Chao Tom (2)<span class="price">9.50</span><span class="desc">Grilled shrimp paste vermicelli bowl</span></span></div>
    <div class="item"><span class="no">40.</span><span class="name">Bun Bo Hue<span class="price">9.50</span><svg class="hot" viewBox="0 0 10 13"><path d="M5 0C6 4 10 5 9 9a4 4 0 0 1-8 0C1 6 3 5 3 3c1 1 2 2 2 3 1-2 0-4 0-6z" fill="var(--chili)"/></svg><span class="desc">Spicy beef noodle soup with beef shank, pork knuckle, pork blood with large vermicelli noodles</span></span></div>
    <div class="item"><span class="no">41.</span><span class="name">Bun Rieu<span class="price">9.50</span><span class="desc">Mixed ground pork &amp; crab, pork blood, dried tofu with vermicelli rice noodle in tomato broth soup</span></span></div>
    <div class="item"><span class="no">42.</span><span class="name">Bun Mang Vit<span class="price">9.50</span><span class="desc">Duck &amp; bamboo vermicelli noodle soup</span></span></div>
  </div>

  <!-- Com Tam -->
  <div class="section-head centered" style="left:900px;top:22px;width:200px">
    <h2 class="heading big">Com Tam</h2>
    <p class="subhead">Broken Rice Plate</p>
  </div>
  <div class="col" style="left:835px;top:96px;width:335px">
    <div class="item"><span class="no">43.</span><span class="name">Com Dac Biet<span class="price">14.95</span><span class="desc">Special rice combination with grilled chicken, grilled pork, grilled shrimp &amp; fried eggroll</span></span></div>
    <div class="item"><span class="no">44.</span><span class="name">Com Suon Nuong Xa<span class="price">9.95</span><span class="desc">Grilled pork chops marinated in lemongrass</span></span></div>
    <div class="item"><span class="no">45.</span><span class="name">Com Suon Bi Cha<span class="price">9.50</span><span class="desc">Grilled pork chop, pork skin roasted with rice powder &amp; eggcake</span></span></div>
    <div class="item" style="margin-bottom:1px"><span class="no">46.</span><span class="name">Com Thit Nuong, Ga Nuong or Bo Nuong<span class="price">9.75</span><span class="desc">Choice of: grilled pork, grilled chicken or grilled beef</span></span></div>
    <div class="item"><span class="no">47.</span><span class="name">+Shrimp<span class="price">10.95</span><span class="desc">Grilled Korean BBQ ribs</span></span></div>
    <div class="item"><span class="no">48.</span><span class="name">Com Suon Dai Han<span class="price">13.95</span><span class="desc">Grilled Korean BBQ ribs</span></span></div>
  </div>
  <div class="photo" role="img" aria-label="Broken rice plate with grilled pork chop, egg cake and pickled vegetables" style="left:1075px;top:212px;width:132px;height:132px;background:radial-gradient(circle at 55% 60%,#7a3a22 0%,#a8643a 30%,#e9d7a8 55%,#f7f1e4 75%)"></div>

  <!-- Com Chien -->
  <div class="section-head inline" style="left:810px;top:320px">
    <h2 class="heading mid">Com Chien</h2>
    <div class="tagline">
      <p class="subhead">Fried Rice</p>
      <p class="note soft" style="width:110px;margin-top:2px">Fried rice is cooked with egg, peas &amp; carrots</p>
    </div>
  </div>
  <div class="col" style="left:836px;top:375px;width:160px">
    <div class="item"><span class="no">49.</span><span class="name">Com Chien Thap Cam<span class="price">10.95</span><span class="desc">House special fried rice with shrimp, roasted pork, sausage with peas &amp; carrots</span></span></div>
    <div class="item"><span class="no">50.</span><span class="name">Com Chien Tom<span class="price">9.95</span><span class="desc">Shrimp fried rice</span></span></div>
    <div class="item"><span class="no">51.</span><span class="name">Com Chien Ga<span class="price">9.95</span><span class="desc">Chicken fried rice</span></span></div>
  </div>
  <div class="col" style="left:1006px;top:375px;width:175px">
    <div class="item"><span class="no">52.</span><span class="name">Com Chien Canh Ga<span class="price">9.50</span><span class="desc">Fried rice with fried chicken wings</span></span></div>
    <div class="item"><span class="no">53.</span><span class="name">Com Chien Bo Luc Lac<span class="price">9.50</span><span class="desc">Shaking beef stir fry filet mignon with bell peppers with fried rice</span></span></div>
    <div class="item"><span class="no">54.</span><span class="name">+ Shrimps<span class="price">16.95</span><span class="desc">Spicy beef noodle soup with beef</span></span></div>
  </div>

  <!-- Xao -->
  <div class="section-head inline" style="left:810px;top:497px">
    <h2 class="heading mid">Xao</h2>
    <div class="tagline">
      <p class="subhead">Stir Fry<br>With Rice<br>Plate</p>
    </div>
  </div>
  <div class="col" style="left:836px;top:550px;width:165px">
    <div class="item"><span class="no">55.</span><span class="name">Ga Xao Gung<span class="price">9.95</span><span class="desc">Stir fry chicken with ginger</span></span></div>
    <div class="item"><span class="no">56.</span><span class="name">Ga or Bo Xao Xa Ot<span class="price">9.95</span><svg class="hot" viewBox="0 0 10 13"><path d="M5 0C6 4 10 5 9 9a4 4 0 0 1-8 0C1 6 3 5 3 3c1 1 2 2 2 3 1-2 0-4 0-6z" fill="var(--chili)"/></svg><span class="desc">Choice of: stir fry chicken or beef in hot chili &amp; lemongrass</span></span></div>
    <div class="item"><span class="no">57.</span><span class="name">Tom Xao Xa Ot<span class="price">10.95</span><svg class="hot" viewBox="0 0 10 13"><path d="M5 0C6 4 10 5 9 9a4 4 0 0 1-8 0C1 6 3 5 3 3c1 1 2 2 2 3 1-2 0-4 0-6z" fill="var(--chili)"/></svg><span class="desc">Stir fry shrimp in hot chilli &amp; lemongrass</span></span></div>
    <div class="item"><span class="no">58.</span><span class="name">Mi Xao Mem or Don Hai San<span class="price">14.95</span><span class="desc">Choice of: soft or crispy noodles stir fry with shrimp, squid, fish ball &amp; imitation crab with vegetables</span></span></div>
    <div class="item"><span class="no">59.</span><span class="name">Ga or Bo Xao Rau Cai<span class="price">9.95</span><span class="desc">Choice of: stir fry chicken or beef with mixed vegetables</span></span></div>
  </div>
  <div class="col" style="left:1006px;top:550px;width:170px">
    <div class="item"><span class="no">60.</span><span class="name">Tom Xao Rau Cai<span class="price">10.95</span><span class="desc">Stir fry shrimp with mixed vegetables</span></span></div>
    <div class="item"><span class="no">61.</span><span class="name">Com Tom Rang Chay Mo<span class="price">10.95</span><span class="desc">Stir fry shrimp, ginger, onion &amp; bell pepper in garlic sauce</span></span></div>
    <div class="item"><span class="no">62</span><span class="name">Canh Chua Ca or Tom<span class="price">10.95</span><span class="desc">Choice of: fish or shrimp soup with tomato, pineapple, okra &amp; bean sprouts served with white rice (serving 2-4)</span></span></div>
    <div class="item"><span class="no">63.</span><span class="name">Ca Kho To<span class="price">10.95</span><span class="desc">Braised swai fish in clay pot with black pepper &amp; dry shallots served with white rice</span></span></div>
  </div>
</main>
</body>
</html>
```